Kelvor Engineers: Why you should hire us keepsake

New design. Open to plastic cards. We are an engineering firm that designs cell phone towers and commercial buildings. Please check out our website www.kelvorstruct.com for more details. We want people to remember our card and for it to be useful if possible. We want the same look and feel on these cards to be translated to other marketing material we may need such as brochures.

Target Market(s)

Architects, Developers and Telecommunication Carriers

Industry/Entity Type

Engineering

Contact Information for Business Card

Card with our company colors, logo, and innovative design with elements related to our industry.

Font styles to use
Sans Serif

Colors
9bcb3c
abd036
0255a3

Requirements
Must have
• Sleek and hip design
Nice to have
• Bright lime green and navy coloring that pops with an innovative design.
Should not have
• A basic and boring design

```html
<!DOCTYPE html>
<html lang="en">
<head>
<meta charset="utf-8">
<title>Kelvor Engineers – Business Card</title>
<link href="https://fonts.googleapis.com/css2?family=Archivo:wght@400;500;700;800&display=swap" rel="stylesheet">
<style>
  :root {
    --navy: #1b3566;
    --lime: #cdd52a;
    --white: #ffffff;
    --stage: #3a3b3d;
  }
  * { margin: 0; padding: 0; box-sizing: border-box; }
  html, body {
    width: 1200px; height: 900px; overflow: hidden;
    background: var(--stage);
    font-family: "Archivo", Arial, sans-serif;
  }
  .stage { position: relative; width: 1200px; height: 900px; }
  .card {
    position: absolute;
    width: 700px; height: 400px;
    border-radius: 26px;
    overflow: hidden;
    box-shadow: 0 14px 30px rgba(0,0,0,.35);
  }
  /* Back */
  .card-back { left: 440px; top: 50px; background: var(--navy); }
  .card-back .brand-name {
    position: absolute; left: 0; right: 0; top: 110px;
    text-align: center;
    color: var(--lime); font-weight: 800; font-size: 66px; letter-spacing: -1px;
  }
  .card-back .office-list {
    position: absolute; left: 50px; bottom: 50px;
    color: var(--white); font-weight: 500; font-size: 21px; letter-spacing: 2px;
  }
  .office-list .divider { color: var(--lime); margin: 0 8px; }
  /* Front */
  .card-front { left: 60px; top: 450px; background: var(--white); }
  .card-front .shapes { position: absolute; inset: 0; }
  .card-front .brand-name {
    position: absolute; left: 40px; top: 32px;
    color: var(--lime); font-weight: 800; font-size: 46px; line-height: 1.0; letter-spacing: -1px;
  }
  .card-front .tagline {
    position: absolute; left: 40px; top: 198px;
    color: var(--navy); font-weight: 500; font-size: 15px; letter-spacing: 2px; white-space: nowrap;
  }
  .holder { position: absolute; right: 30px; top: 108px; text-align: right; }
  .holder .holder-name { color: var(--navy); font-weight: 700; font-size: 24px; line-height: 30px; white-space: nowrap; }
  .holder .holder-title { color: var(--white); font-size: 16px; line-height: 20px; }
  .contact-list {
    position: absolute; right: 28px; top: 304px;
    list-style: none; color: var(--white); font-size: 16px; line-height: 21px;
  }
  .contact-list li { display: flex; justify-content: flex-end; align-items: center; gap: 12px; white-space: nowrap; }
  .contact-list svg { width: 13px; height: 13px; flex: none; }
</style>
</head>
<body>
<div class="stage">

  <section class="card card-back">
    <div class="brand-name">Kelvor Engineers</div>
    <div class="office-list">ATLANTA<span class="divider">/</span>CHARLOTTE<span class="divider">/</span>HOUSTON<span class="divider">/</span>SAN ANTONIO</div>
  </section>

  <section class="card card-front">
    <svg class="shapes" viewBox="0 0 700 400" preserveAspectRatio="none">
      <path d="M280 0 C300 150 450 210 700 220 L700 0 Z" fill="var(--lime)"/>
      <path d="M266 0 C286 158 450 226 700 236 L700 220 C450 210 300 150 280 0 Z" fill="var(--navy)"/>
      <path d="M0 230 C250 228 500 250 700 290 L700 400 L0 400 Z" fill="var(--lime)"/>
      <path d="M0 240 C250 240 500 262 700 300 L700 400 L0 400 Z" fill="var(--navy)"/>
    </svg>
    <div class="brand-name">Kelvor<br>Engineers</div>
    <div class="tagline">MULTI-DISCIPLINE ENGINEERING</div>
    <div class="holder">
      <div class="holder-name">Dana Rooke Ellery</div>
      <div class="holder-title">Director</div>
    </div>
    <ul class="contact-list">
      <li>555.014.2290
        <svg viewBox="0 0 16 16"><path d="M3 1l3 3-1.5 2a9 9 0 0 0 5.5 5.5L12 10l3 3-2 2C6 15 1 10 1 3z" fill="var(--lime)"/></svg></li>
      <li>555.018.7731
        <svg viewBox="0 0 16 16"><rect x="4" y="1" width="8" height="14" rx="1.5" fill="none" stroke="var(--lime)" stroke-width="1.6"/></svg></li>
      <li>dellery@kelvorstruct.com
        <svg viewBox="0 0 16 16"><rect x="1" y="3" width="14" height="10" fill="none" stroke="var(--lime)" stroke-width="1.6"/><path d="M1 3l7 6 7-6" fill="none" stroke="var(--lime)" stroke-width="1.6"/></svg></li>
      <li>www.kelvorstruct.com
        <svg viewBox="0 0 16 16"><circle cx="8" cy="8" r="6.5" fill="none" stroke="var(--lime)" stroke-width="1.5"/><path d="M1.5 8h13M8 1.5c-3 3.5-3 9.5 0 13M8 1.5c3 3.5 3 9.5 0 13" fill="none" stroke="var(--lime)" stroke-width="1.2"/></svg></li>
    </ul>
  </section>

</div>
</body>
</html>
```